Brintel Works - Fast, Efficient and Gas Mainteance for Domestic, Commercial and Industrial clients

We are in the process of purchasing a new business and would like to get a new logo and business card.
Business is a gas maintenance business that also does new gas installations.
Has been established since 1988.
Services include:
Install all types of gas appliances & equipment inc. hot water units
Maintain / repair / replace all types of gas appliances & equipment

Target Market(s)

Domestic, Commercial and Industrial clients

Industry/Entity Type

Business

Contact Information for Business Card

admin@brintelworks.com.au
07 3918 4726
Brintel Works PTY LTD

Logo Text

Gas Fitting & Plumbing Maintenance Specialists

Font styles to use
Sans Serif

Requirements
Must have
• Logo
• Business name, contact number, email address, web address
• Domestic | Commercial | Industrial Est Since 1988
Nice to have
• Possibly a black card with a flame logo to one side
Should not have
• Spelling errors

```html
<!DOCTYPE html>
<html lang="en">
<head>
<meta charset="utf-8">
<title>Brintel Works – Business Card</title>
<link href="https://fonts.googleapis.com/css2?family=Merriweather:wght@700&family=Open+Sans:wght@400;600&family=Great+Vibes&display=swap" rel="stylesheet">
<style>
  :root {
    --page-bg: #e7e5e2;
    --card-black: #0d0d0d;
    --card-white: #f7f7f7;
    --panel-white: #fbfbfb;
    --brand-orange: #e4623f;
    --ink-slate: #3d4456;
    --ink-dark: #1c1c1c;
    --ink-muted: #8b8b8b;
    --watermark: rgba(0,0,0,0.05);
  }
  * { box-sizing: border-box; margin: 0; padding: 0; }
  html, body { width: 1200px; height: 892px; overflow: hidden; }
  body {
    background: var(--page-bg);
    font-family: "Open Sans", sans-serif;
    position: relative;
  }
  .card {
    position: absolute;
    top: 291px;
    width: 540px;
    height: 310px;
    border-radius: 18px;
    overflow: hidden;
    box-shadow: 0 6px 18px rgba(0,0,0,0.18);
  }
  /* Front */
  .card-front { left: 40px; background: var(--card-black); }
  .front-tab {
    position: absolute; right: 0; top: 0;
    width: 38px; height: 118px;
    background: #e6e6e6;
    border-bottom-left-radius: 12px;
  }
  .front-mark {
    position: absolute; left: 392px; top: 60px; width: 110px;
    display: flex; align-items: center; gap: 8px;
    color: #ffffff; font-family: "Open Sans", sans-serif;
    font-weight: 600; font-size: 15px; line-height: 1.2;
  }
  .front-mark .dot { width: 12px; height: 12px; border-radius: 50%; background: #ffffff; flex: none; }
  .info-panel {
    position: absolute; left: 22px; top: 40px;
    width: 356px; height: 248px;
    background: var(--panel-white);
    border-radius: 14px;
    padding: 22px 20px 18px 22px;
  }
  .brand-name {
    font-family: "Merriweather", serif; font-weight: 700;
    color: var(--brand-orange); text-transform: uppercase;
    font-size: 23px; letter-spacing: 0.5px; line-height: 1;
    display: flex; align-items: flex-end; gap: 6px;
  }
  .brand-name .legal { font-family: "Open Sans", sans-serif; font-size: 6px; color: var(--ink-slate); font-weight: 600; letter-spacing: 0.4px; margin-bottom: 14px; }
  .tagline { color: var(--ink-slate); font-weight: 600; font-size: 14.5px; margin-top: 4px; }
  .sectors { display: flex; align-items: baseline; gap: 12px; margin-top: 1px; }
  .sectors .list { font-size: 7.5px; color: var(--ink-muted); }
  .sectors .est { font-family: "Great Vibes", cursive; font-size: 15px; color: #a9a9a9; }
  .contacts { list-style: none; margin-top: 16px; text-align: right; }
  .contacts li { display: flex; justify-content: flex-end; align-items: center; gap: 9px; font-size: 12px; color: var(--ink-dark); line-height: 19px; }
  .contacts .icon { width: 12px; height: 12px; background: var(--ink-dark); border-radius: 2px; display: flex; align-items: center; justify-content: center; flex: none; }
  .contacts .icon svg { width: 8px; height: 8px; }
  /* Back */
  .card-back { left: 620px; background: linear-gradient(135deg, #ffffff 0%, var(--card-white) 55%, #e4e4e4 100%); }
  .back-watermark {
    position: absolute; right: 24px; bottom: 34px;
    font-family: "Open Sans", sans-serif; font-weight: 600;
    font-size: 40px; color: var(--watermark);
  }
  .back-content { position: absolute; left: 52px; top: 84px; }
  .back-content .brand-name { font-size: 36px; }
  .back-content .brand-name .legal { font-size: 8px; margin-bottom: 22px; }
  .back-content .tagline { font-size: 21px; margin-top: 6px; }
  .back-content .sectors .list { font-size: 10px; }
  .back-content .sectors .est { font-size: 22px; }
</style>
</head>
<body>
  <section class="card card-front" aria-label="Business card front">
    <div class="front-tab"></div>
    <div class="front-mark"><span class="dot"></span><span>Brintel Works</span></div>
    <div class="info-panel">
      <div class="brand-name">Brintel Works<span class="legal">PTY LTD</span></div>
      <div class="tagline">Gas fitting &amp; Plumbing Specialists</div>
      <div class="sectors"><span class="list">Domestic | Commercial | Industrial</span><span class="est">Est Since 1988</span></div>
      <ul class="contacts">
        <li>07 3918 4726<span class="icon"><svg viewBox="0 0 8 8"><path d="M1 1h2l1 2-1 1q1 1.5 2 2l1-1 2 1v2h-1Q2 7.5 1 2z" fill="#fff"/></svg></span></li>
        <li>07 3918 4735<span class="icon"><svg viewBox="0 0 8 8"><rect x="1" y="3" width="6" height="4" fill="#fff"/><rect x="2" y="1" width="4" height="2" fill="#fff"/></svg></span></li>
        <li>www.brintelworks.com.au<span class="icon"><svg viewBox="0 0 8 8"><circle cx="4" cy="4" r="3" fill="none" stroke="#fff"/></svg></span></li>
        <li>admin@brintelworks.com.au<span class="icon"><svg viewBox="0 0 8 8"><rect x="1" y="2" width="6" height="4" fill="none" stroke="#fff" stroke-width="0.8"/><path d="M1 2l3 2 3-2" fill="none" stroke="#fff" stroke-width="0.8"/></svg></span></li>
        <li>PO Box 2846, Coral Bay, QLD 4227<span class="icon"><svg viewBox="0 0 8 8"><path d="M4 7Q1.5 4 1.5 3a2.5 2.5 0 0 1 5 0Q6.5 4 4 7z" fill="#fff"/></svg></span></li>
      </ul>
    </div>
  </section>

  <section class="card card-back" aria-label="Business card back">
    <div class="back-watermark">Brintel Works</div>
    <div class="back-content">
      <div class="brand-name">Brintel Works<span class="legal">PTY LTD</span></div>
      <div class="tagline">Gas fitting &amp; Plumbing Specialists</div>
      <div class="sectors"><span class="list">Domestic | Commercial | Industrial</span><span class="est">Est Since 1988</span></div>
    </div>
  </section>
</body>
</html>
```